RTavenor Business Cards & Letterhead

I have a logo but need a design for some new business cards. We are a Design-Build Firm that specializes in the design and construction of commercial projects.
the cards need to be professional. no cartoon stuff.
i would like to have the cards in AI format so I can update the card as needed. Logo is provided.
Our Address is: 4187 Marlowe Ct. Corrin Bay, Eastmoor 27614

```html
<!DOCTYPE html>
<html lang="en">
<head>
<meta charset="utf-8">
<title>RTavenor Business Cards</title>
<link rel="stylesheet" href="https://fonts.googleapis.com/css2?family=Open+Sans:wght@400;600;700&display=swap">
<style>
  :root {
    --backdrop: #1f2227;
    --card: #ffffff;
    --brand-blue: #0f5d9c;
    --ink: #1d1d1f;
    --wordmark-grey: #4a4b4e;
    --rule: #b9bcc0;
  }
  * { box-sizing: border-box; margin: 0; padding: 0; }
  html, body { width: 1200px; height: 780px; overflow: hidden; }
  body {
    background: var(--backdrop);
    font-family: "Open Sans", Arial, sans-serif;
    display: flex;
    align-items: center;
    justify-content: center;
    gap: 60px;
  }
  .card {
    width: 525px;
    height: 300px;
    background: var(--card);
    position: relative;
    box-shadow: 0 12px 30px rgba(0,0,0,.45);
  }
  .card-contact { display: flex; align-items: center; }
  .brand-block {
    width: 230px;
    display: flex;
    align-items: center;
    justify-content: center;
  }
  .brand-block .brand-name {
    font-weight: 700;
    font-size: 36px;
    color: var(--brand-blue);
    letter-spacing: .5px;
  }
  .divider {
    width: 1px;
    height: 190px;
    background: linear-gradient(var(--card), var(--rule) 30%, var(--rule) 70%, var(--card));
  }
  .details { padding-left: 26px; color: var(--ink); }
  .person-name {
    font-weight: 700;
    font-size: 24px;
    color: var(--brand-blue);
    letter-spacing: 1px;
    line-height: 1.1;
  }
  .person-title { font-weight: 600; font-size: 15px; margin-bottom: 6px; }
  .address { font-size: 15px; line-height: 1.3; margin-bottom: 4px; }
  .contact-list { list-style: none; font-size: 15px; line-height: 1.35; }
  .contact-list li { display: flex; align-items: center; gap: 6px; }
  .contact-list svg { width: 13px; height: 13px; flex: none; }
  .card-wordmark { display: flex; align-items: center; justify-content: center; }
  .wordmark { display: flex; align-items: center; gap: 14px; }
  .wordmark-square { width: 34px; height: 34px; background: var(--brand-blue); }
  .wordmark-name {
    font-weight: 700;
    font-size: 54px;
    color: var(--wordmark-grey);
    letter-spacing: 1px;
  }
</style>
</head>
<body>
  <section class="card card-contact">
    <div class="brand-block"><span class="brand-name">RTavenor</span></div>
    <div class="divider"></div>
    <div class="details">
      <p class="person-name">DALTON TAVENOR</p>
      <p class="person-title">Founder/President</p>
      <p class="address">4187 Marlowe Ct. Corrin Bay,<br>Eastmoor 27614</p>
      <ul class="contact-list">
        <li>
          <svg viewBox="0 0 16 16" aria-hidden="true"><path fill="#0f5d9c" d="M3.6 1.5l2.3 2.6-1.3 1.7c.9 2 2.6 3.7 4.6 4.6l1.7-1.3 2.6 2.3-1.2 2.3C6.9 15.2.8 9.1.9 2.7z"/></svg>
          (555) 214-0148
        </li>
        <li>
          <svg viewBox="0 0 16 16" aria-hidden="true"><circle cx="8" cy="8" r="6.5" fill="none" stroke="#0f5d9c" stroke-width="1.6"/><ellipse cx="8" cy="8" rx="2.8" ry="6.5" fill="none" stroke="#0f5d9c" stroke-width="1.2"/><path d="M1.5 8h13" stroke="#0f5d9c" stroke-width="1.2"/></svg>
          www.rtavenor.com
        </li>
        <li>
          <svg viewBox="0 0 16 16" aria-hidden="true"><rect x="1" y="3" width="14" height="10" rx="1" fill="#0f5d9c"/><path d="M1.5 3.8L8 9l6.5-5.2" fill="none" stroke="#fff" stroke-width="1.2"/></svg>
          DTT@RTavenor.com
        </li>
      </ul>
    </div>
  </section>

  <section class="card card-wordmark">
    <div class="wordmark">
      <span class="wordmark-square"></span>
      <span class="wordmark-name">RTavenor</span>
    </div>
  </section>
</body>
</html>
```